Business Card Design Project

Business Card
We are rebranding with a new logo
Industry/Entity Type
Business
Contact Information for Business Card
Dennis Morvale +61 487215963 dennis@quorv.com.au P.O. Box 872 Fernlow QLD 4309
Requirements
Must have
- Logo

```html
<!DOCTYPE html>
<html lang="en">
<head>
<meta charset="utf-8">
<title>Quorv International – Business Card</title>
<link rel="stylesheet" href="https://fonts.googleapis.com/css2?family=Roboto:wght@400;500&display=swap">
<style>
  :root {
    --page-bg: #e4e4e2;
    --card-bg: #f4f4f3;
    --brand-blue: #1a8fce;
    --name-blue: #1d9ad8;
    --text-grey: #4a4a4a;
  }
  * { margin: 0; padding: 0; box-sizing: border-box; }
  html, body {
    width: 1200px;
    height: 960px;
    overflow: hidden;
    background: var(--page-bg);
    font-family: "Roboto", Arial, sans-serif;
  }
  .business-card {
    position: absolute;
    left: 300px;
    top: 309px;
    width: 600px;
    height: 342px;
    background: var(--card-bg);
    border-radius: 16px;
    box-shadow: 0 2px 6px rgba(0,0,0,0.12);
  }
  .brand {
    position: absolute;
    left: 42px;
    top: 142px;
    color: var(--brand-blue);
    font-weight: 500;
  }
  .brand-name {
    display: block;
    font-size: 58px;
    line-height: 1;
    letter-spacing: -0.5px;
  }
  .brand-descriptor {
    display: block;
    margin-top: 12px;
    font-size: 17px;
    letter-spacing: 3.2px;
  }
  .contact-block {
    position: absolute;
    right: 24px;
    top: 183px;
    text-align: right;
    color: var(--text-grey);
  }
  .person-name {
    color: var(--name-blue);
    font-weight: 500;
    font-size: 20px;
    letter-spacing: 0.2px;
    margin-bottom: 12px;
  }
  .address-line {
    font-size: 14.5px;
    line-height: 18px;
  }
  .contact-list {
    list-style: none;
    margin-top: 8px;
  }
  .contact-item {
    display: flex;
    justify-content: flex-end;
    align-items: center;
    gap: 7px;
    font-size: 14.5px;
    line-height: 19.5px;
  }
  .contact-icon {
    width: 13px;
    height: 13px;
    fill: var(--name-blue);
    flex: none;
  }
</style>
</head>
<body>
  <div class="business-card">
    <div class="brand">
      <span class="brand-name">Quorv</span>
      <span class="brand-descriptor">INTERNATIONAL</span>
    </div>

    <div class="contact-block">
      <p class="person-name">DENNIS MORVALE</p>
      <p class="address-line">P.O. Box 872</p>
      <p class="address-line">Fernlow QLD 4309</p>
      <ul class="contact-list">
        <li class="contact-item">
          <span>+61 487215963</span>
          <svg class="contact-icon" viewBox="0 0 24 24" aria-hidden="true"><path d="M6.6 10.8a15.1 15.1 0 0 0 6.6 6.6l2.2-2.2a1 1 0 0 1 1-.25 11.4 11.4 0 0 0 3.6.57 1 1 0 0 1 1 1V20a1 1 0 0 1-1 1A17 17 0 0 1 3 4a1 1 0 0 1 1-1h3.5a1 1 0 0 1 1 1c0 1.25.2 2.45.57 3.6a1 1 0 0 1-.25 1z"/></svg>
        </li>
        <li class="contact-item">
          <span>dennis@quorv.com.au</span>
          <svg class="contact-icon" viewBox="0 0 24 24" aria-hidden="true"><path d="M2 5h20v14H2z M3.5 6.5 12 12.5l8.5-6" fill="none" stroke="#1d9ad8" stroke-width="0"/><path d="M2 5h20v2l-10 6.5L2 7z"/><path d="M2 9l10 6.5L22 9v10H2z"/></svg>
        </li>
        <li class="contact-item">
          <span>www.quorv.com.au</span>
          <svg class="contact-icon" viewBox="0 0 24 24" aria-hidden="true"><circle cx="12" cy="12" r="11"/><path d="M12 1v22M1 12h22M12 1c-4 4-4 18 0 22M12 1c4 4 4 18 0 22" fill="none" stroke="#f4f4f3" stroke-width="1.4"/></svg>
        </li>
      </ul>
    </div>
  </div>
</body>
</html>
```